Kestrel Finish Studio (KFS)

I would like to design a dedicated site for my KFS product, which allows industry employees to be trained in the visual inspection of mechanical parts. My product is a 3D simulator (see https://morvint-works.ch/our-applications/virtual-reality/ and https://morvint-works.ch for videos) which makes it possible to manufacture standard parts representative of a type of defect which is accepted or refused by the quality department. These master parts can be used to create a common quality culture in the company and to train employees in a homogeneous way. The simulator is initially designed for watchmaking, but must be designed for much broader industries (cars, phone reconditioning, ball bearings, etc.)
L'information que j'ai donnée n'est pas assez précise. Je dois préciser les domaines métiers visés par le site internet. J'ai besoin de quelques jours pour choisir les domaines les plus représentatifs.
Coded - Design and coding required
1 page

```html
<!DOCTYPE html>
<html lang="en">
<head>
<meta charset="utf-8">
<title>Kestrel Finish Studio</title>
<link href="https://fonts.googleapis.com/css2?family=Poppins:wght@400;500;600;700&display=swap" rel="stylesheet">
<style>
:root{
  --blue:#1270c2;
  --blue-dark:#0a5aa3;
  --ink:#111;
  --text:#333;
  --white:#fff;
  --footer:#0b0b0b;
  --star:#f5b800;
}
*{box-sizing:border-box;margin:0;padding:0}
html,body{width:1200px;height:4118px;overflow:hidden}
body{font-family:"Poppins",sans-serif;color:var(--text);background:var(--white);position:relative}
.abs{position:absolute}
a{color:inherit;text-decoration:none}

/* header */
.brand{left:100px;top:18px;font-weight:600;font-size:27px;line-height:32px;color:var(--ink);text-align:center;width:230px}
.brand span{color:var(--blue)}
.social-top{left:418px;top:8px;display:flex;gap:15px}
.dot{width:32px;height:32px;border-radius:50%;background:var(--blue)}
.contact-top{top:8px;display:flex;align-items:center;gap:8px;font-size:15px;color:var(--ink)}
.ring{width:36px;height:36px;border-radius:50%;border:2px solid var(--blue);display:flex;align-items:center;justify-content:center}
.nav{left:372px;top:48px;width:728px;height:50px;border-radius:25px;background:var(--blue);display:flex;align-items:center;padding-left:93px;gap:38px;color:var(--white);font-size:15px;font-weight:500}
.nav .active{font-weight:700;font-size:17px;text-decoration:underline;text-underline-offset:5px}

/* hero */
.hero{left:0;top:99px;width:1200px;height:601px;background:linear-gradient(120deg,#3a3f46 0%,#6b4a52 35%,#2c2e3a 60%,#bcbfc4 100%)}
.hero-shade{left:0;top:99px;width:1200px;height:601px;background:rgba(0,0,0,.28)}
.hero-title{left:0;top:344px;width:1200px;text-align:center;color:var(--white);font-size:56px;line-height:68px;font-weight:600;text-shadow:0 2px 6px rgba(0,0,0,.35)}
.hero-sub{left:0;top:420px;width:1200px;text-align:center;color:var(--white);font-size:14px}
.btn{display:inline-block;background:var(--blue);color:var(--white);font-weight:600;font-size:18px;border-radius:26px;padding:0 26px;line-height:50px;box-shadow:0 4px 8px rgba(0,0,0,.2)}

/* intro */
.photo{border-radius:26px}
.h2{font-size:33px;font-weight:600;line-height:35px;color:var(--ink)}
.h2 span{color:var(--blue)}
.para{font-size:14px;line-height:31px;color:var(--text)}
.para .link{color:var(--blue)}

/* control band */
.band-title{left:0;top:1383px;width:1200px;text-align:center;color:var(--white);font-size:31px;font-weight:600}
.feature{width:290px;text-align:center;color:var(--white);font-size:15px;font-weight:500;line-height:27px}
.icon{width:140px;height:140px}

/* card */
.card{left:145px;top:2060px;width:898px;height:518px;background:var(--white);border-radius:28px;box-shadow:0 6px 30px rgba(0,0,0,.12)}

/* testimonials */
.testimonials-title{left:0;top:2718px;width:1200px;text-align:center;color:var(--white);font-size:32px;line-height:46px;font-weight:600}
.quote-card{left:328px;top:2828px;width:549px;height:315px;background:var(--white)}
.avatar{border-radius:50%;border:5px solid var(--white);background:linear-gradient(160deg,#c9c9cc,#7a6f6a)}

/* footer */
.footer{left:0;top:3705px;width:1200px;height:413px;background:var(--footer);color:var(--white)}
.footer h4{font-size:19px;font-weight:600;text-transform:uppercase}
.footer li{list-style:none;font-size:15px;line-height:31px}
.fdot{width:44px;height:44px;border-radius:50%;border:2px solid var(--white)}
</style>
</head>
<body>

<!-- header -->
<div class="abs brand">Kestrel Finish<br><span>Studio</span></div>
<div class="abs social-top"><div class="dot"></div><div class="dot"></div><div class="dot"></div><div class="dot"></div></div>
<div class="abs contact-top" style="left:615px">
  <div class="ring"><svg width="16" height="16" viewBox="0 0 24 24"><path d="M6.6 10.8a15 15 0 0 0 6.6 6.6l2.2-2.2c.3-.3.7-.4 1-.2 1.1.4 2.3.6 3.6.6.6 0 1 .4 1 1V20c0 .6-.4 1-1 1A17 17 0 0 1 3 4c0-.6.4-1 1-1h3.5c.6 0 1 .4 1 1 0 1.3.2 2.5.6 3.6.1.3 0 .7-.2 1z" fill="#1270c2"/></svg></div>+1 555 014 2290</div>
<div class="abs contact-top" style="left:800px">
  <div class="ring"><svg width="18" height="14" viewBox="0 0 24 18"><rect x="1" y="1" width="22" height="16" rx="2" fill="#1270c2"/><path d="M2 2l10 8 10-8" stroke="#fff" stroke-width="2" fill="none"/></svg></div>hello@kestrelfinish.example</div>
<nav class="abs nav"><a class="active">Home</a><a>About Us</a><a>How Its Works</a><a>Services</a><a>Contact Us</a></nav>

<!-- hero -->
<div class="abs hero" role="img" aria-label="Watchmaker assembling a wristwatch at a workbench"></div>
<div class="abs hero-shade"></div>
<h1 class="abs hero-title">Kestrel Finish Studio</h1>
<p class="abs hero-sub">Virtual Reality The Services Of Controlled Aesthetic Watchmaking</p>
<div class="abs" style="left:0;top:457px;width:1200px;text-align:center"><a class="btn" style="line-height:49px">Get Started</a></div>

<!-- intro -->
<div class="abs" style="left:200px;top:795px;width:385px;height:416px;background:var(--blue);border-radius:26px 26px 40px 26px"></div>
<div class="abs photo" style="left:78px;top:828px;width:247px;height:410px;border:4px solid #fff;background:linear-gradient(150deg,#d9d4cf,#6d7680 60%,#c9c4be)" role="img" aria-label="Watchmaker with loupe working on a movement"></div>
<div class="abs photo" style="left:322px;top:758px;width:247px;height:410px;border:4px solid #fff;background:linear-gradient(160deg,#3a3a3a,#8d8d8d 55%,#2a2a2a)" role="img" aria-label="Hand holding an open watch movement"></div>
<h2 class="abs h2" style="left:615px;top:770px">Lighten the <span>management</span> of<br><span>physical</span> components</h2>
<p class="abs para" style="left:617px;top:847px;width:500px">Aesthetic defects are often the result of careless handling of the components and products concerned, whether during manufacture, assembly or marketing. By making the KFS platform available to staff in direct contact with the product, it becomes very easy to make them aware of the evaluation criteria and the aesthetic vocabulary defined by the company.<span class="link">Improve after-sales service returns</span>:The KFS platform can easily be used by the service network staff<br>to assist them in the objective assessment of aesthetic defects<br>by referring to the semantic matrix as well as to the cases<br>already referenced.</p>
<div class="abs" style="left:615px;top:1176px"><a class="btn">Read More</a></div>

<!-- control band -->
<svg class="abs" style="left:0;top:1290px" width="1200" height="836"><path d="M0 0H145L180 46H1200V836H0Z" fill="#1270c2"/></svg>
<div class="abs" style="left:0;top:1290px;width:1200px;height:836px;background:radial-gradient(circle at 55% 45%,rgba(255,255,255,.08),transparent 55%)" role="img" aria-label="Faint watch movement backdrop"></div>
<h2 class="abs band-title">Aesthetic Control: HOW TO CONTROL IT?</h2>

<svg width="0" height="0" style="position:absolute">
  <defs>
    <g id="badge"><circle cx="62" cy="78" r="62" fill="#fff"/><circle cx="72" cy="68" r="63" fill="#1270c2"/><circle cx="72" cy="68" r="56" fill="none" stroke="#fff" stroke-width="3"/></g>
  </defs>
</svg>

<!-- row 1 -->
<svg class="abs icon" style="left:173px;top:1454px" viewBox="0 0 140 140"><use href="#badge"/><g stroke="#fff" stroke-width="3" fill="none"><circle cx="58" cy="56" r="9"/><circle cx="86" cy="62" r="11"/><circle cx="72" cy="88" r="14"/><path d="M58 42v-5M58 75v-5M44 56h-5M77 56h-5M86 46v-5M86 83v-5M70 62h-5M107 62h-5M72 88l6-6"/></g></svg>
<svg class="abs icon" style="left:541px;top:1454px" viewBox="0 0 140 140"><use href="#badge"/><g stroke="#fff" stroke-width="3" fill="none"><circle cx="72" cy="74" r="26"/><circle cx="72" cy="74" r="19"/><path d="M72 48v-8M64 40h16M72 74l-7-9M94 52l5-5"/></g></svg>
<svg class="abs icon" style="left:910px;top:1454px" viewBox="0 0 140 140"><use href="#badge"/><g stroke="#fff" stroke-width="3" fill="none"><rect x="48" y="46" width="52" height="40" rx="3"/><path d="M58 56h10v10H58zM76 56h10v10H76zM58 72h28"/><circle cx="52" cy="84" r="11"/><path d="M52 84l4-5"/></g></svg>
<p class="abs feature" style="left:94px;top:1598px">Adopting a simple and unambiguous language common understanding of aesthetic quality at the extended enterprise level.</p>
<p class="abs feature" style="left:462px;top:1598px">By using a semantic reference matrix associating the types ofanomalies (scratches,deformations,stains, etc.) ntensity levels defined company.</p>
<p class="abs feature" style="left:831px;top:1598px;width:290px">Determining the compliance thresholds of the component or product.</p>

<!-- row 2 -->
<svg class="abs icon" style="left:173px;top:1740px" viewBox="0 0 140 140"><use href="#badge"/><g stroke="#fff" stroke-width="3" fill="none"><circle cx="72" cy="68" r="32"/><circle cx="72" cy="68" r="25"/><path d="M72 68l14-12M56 68h4M84 68h4M72 52v4"/><circle cx="72" cy="68" r="3" fill="#fff"/></g></svg>
<svg class="abs icon" style="left:541px;top:1740px" viewBox="0 0 140 140"><use href="#badge"/><g stroke="#fff" stroke-width="3" fill="none"><rect x="62" y="36" width="20" height="14" rx="3"/><rect x="62" y="86" width="20" height="14" rx="3"/><circle cx="72" cy="68" r="18"/><path d="M64 68l5 5 10-10M92 66v5"/></g></svg>
<svg class="abs icon" style="left:910px;top:1740px" viewBox="0 0 140 140"><use href="#badge"/><g stroke="#fff" stroke-width="3" fill="none"><path d="M48 50l10-6 10 6v11l-10 6-10-6z"/><path d="M56 70v16h8M70 82h18l8-4v12H70z"/><circle cx="84" cy="56" r="2"/><circle cx="96" cy="60" r="2"/></g></svg>
<p class="abs feature" style="left:94px;top:1884px">Providing uniform training in operational competence for those responsible for aesthetic control.</p>
<p class="abs feature" style="left:462px;top:1884px">By designing realistic and attractive teaching sequences for total quality control.</p>
<p class="abs feature" style="left:831px;top:1884px">By regularly assessing the competence to measure the aesthetics, expressed in a tangible, r (R&amp;R), of a component or product.</p>

<!-- card -->
<div class="abs card"></div>
<h2 class="abs h2" style="left:180px;top:2108px">Improve after-<span>sales</span><br><span>service</span> returns</h2>
<p class="abs para" style="left:182px;top:2184px;width:420px">The KFS platform can easily be used by the service network staff to assist them in the objective assessment of aesthetic defects by referring to the semantic matrix as well as to the cases already referenced. It is also possible, in an intuitive and playful way, to indicate, in<br>accordance with the product nomenclature, a type of imperfection, its intensity and its location. It is also possible to draw up a precise repair estimate or to declare a<br>non-conformity on a product coming from a market return.</p>
<div class="abs" style="left:182px;top:2476px"><a class="btn">Read More</a></div>
<div class="abs" style="left:620px;top:2102px;width:387px;height:433px;border-radius:26px;background:radial-gradient(ellipse at 55% 45%,#7a5418 0%,#2a1c08 35%,#050505 70%)" role="img" aria-label="Video still of a gold watch case ring"></div>
<svg class="abs" style="left:787px;top:2292px" width="54" height="54"><circle cx="27" cy="27" r="26" fill="#fff"/><path d="M21 16l17 11-17 11z" fill="#111"/></svg>

<!-- testimonials -->
<svg class="abs" style="left:0;top:2637px" width="1200" height="605"><path d="M0 0H145L160 40H1200V605H765L735 558H0Z" fill="#1270c2"/></svg>
<h2 class="abs testimonials-title">Testimonials</h2>
<div class="abs avatar" style="left:98px;top:2817px;width:120px;height:120px" role="img" aria-label="Client portrait"></div>
<div class="abs avatar" style="left:200px;top:2974px;width:96px;height:96px" role="img" aria-label="Client portrait"></div>
<div class="abs avatar" style="left:983px;top:2817px;width:120px;height:120px" role="img" aria-label="Client portrait"></div>
<div class="abs avatar" style="left:907px;top:2974px;width:96px;height:96px" role="img" aria-label="Client portrait"></div>
<div class="abs quote-card"></div>
<div class="abs avatar" style="left:548px;top:2784px;width:112px;height:112px" role="img" aria-label="Reviewer portrait"></div>
<p class="abs" style="left:355px;top:2905px;width:495px;text-align:center;font-size:14px;line-height:26px;color:#333">"In the implementation of the new Qualiticien-nes en microtechnique course, the Lakeside School of Horology has deployed the KFS application to teach the methods of aestheticcontrol. This application fully meets thepedagogical objectives as well as the ease of use by both our teaching staff and our students."</p>
<div class="abs" style="left:328px;top:3060px;width:549px;height:2px;background:#bbb"></div>
<div class="abs" style="left:405px;top:3055px;font-size:90px;color:#c9c9c9;font-weight:700;line-height:1">“</div>
<div class="abs" style="left:730px;top:3055px;font-size:90px;color:#c9c9c9;font-weight:700;line-height:1">”</div>
<p class="abs" style="left:328px;top:3073px;width:549px;text-align:center;font-size:15px;color:#111"><b style="font-weight:600">Maren Okafor</b> <span style="font-size:13px">-United States</span></p>
<p class="abs" style="left:328px;top:3096px;width:549px;text-align:center;font-size:16px;color:var(--star);letter-spacing:4px">★★★★★</p>

<!-- KFS allows -->
<h2 class="abs" style="left:99px;top:3300px;font-size:33px;font-weight:600;color:#111">KFS allows</h2>
<p class="abs para" style="left:99px;top:3347px;width:495px">Remove the management of components used as standards for aesthetic control trainingTo make employees aware of aesthetic control and the vocabulary to be used Integrate aesthetic control into a total quality management (TQM) approach with precise indicators at all stages of the manufacturing and after-sales processes Provide the after-sales service with an efficient tool to record the aesthetic aspect of the supported product</p>
<div class="abs" style="left:99px;top:3577px"><a class="btn">Read More</a></div>
<div class="abs" style="left:740px;top:3290px;width:360px;height:333px;background:var(--blue);border-radius:36px"></div>
<div class="abs" style="left:715px;top:3306px;width:362px;height:336px;border-radius:34px;background:radial-gradient(ellipse at 45% 45%,#a06a3a 0%,#4a3020 40%,#15100c 80%)" role="img" aria-label="Watchmaker with loupe inspecting parts under a lamp"></div>

<!-- footer -->
<footer class="abs footer">
  <div class="abs" style="left:98px;top:98px;font-size:31px;font-weight:600;line-height:35px;text-align:center;width:260px">Kestrel Finish<br>Studio</div>
  <p class="abs" style="left:103px;top:182px;font-size:15px;line-height:36px">
    <svg width="11" height="15" viewBox="0 0 12 16"><path d="M6 0a6 6 0 0 0-6 6c0 4.5 6 10 6 10s6-5.5 6-10a6 6 0 0 0-6-6zm0 8.5A2.5 2.5 0 1 1 6 3.5a2.5 2.5 0 0 1 0 5z" fill="#fff"/></svg>
    Kestrel Finish Studio,<br>&nbsp;&nbsp;&nbsp;48 Harbor Lane.</p>
  <p class="abs" style="left:103px;top:262px;font-size:15px"><svg width="13" height="13" viewBox="0 0 24 24"><path d="M6.6 10.8a15 15 0 0 0 6.6 6.6l2.2-2.2c.3-.3.7-.4 1-.2 1.1.4 2.3.6 3.6.6.6 0 1 .4 1 1V20c0 .6-.4 1-1 1A17 17 0 0 1 3 4c0-.6.4-1 1-1h3.5c.6 0 1 .4 1 1 0 1.3.2 2.5.6 3.6.1.3 0 .7-.2 1z" fill="#fff"/></svg> +1-555-014-2290</p>
  <p class="abs" style="left:103px;top:305px;font-size:15px"><svg width="14" height="11" viewBox="0 0 24 18"><rect x="1" y="1" width="22" height="16" rx="2" fill="#fff"/><path d="M2 2l10 8 10-8" stroke="#0b0b0b" stroke-width="2" fill="none"/></svg> hello@kestrelfinish.example</p>

  <h4 class="abs" style="left:454px;top:110px">Quick Links</h4>
  <ul class="abs" style="left:455px;top:147px"><li>Home</li><li>About</li><li>How Its Works</li><li>Services</li><li>Contact</li></ul>
  <h4 class="abs" style="left:632px;top:110px">Other Links</h4>
  <ul class="abs" style="left:632px;top:147px"><li>Privacy Policy</li><li>Tearms of use</li><li>Terms &amp; Condition</li><li>FAQs</li></ul>
  <h4 class="abs" style="left:831px;top:110px">Subscribe to Newsletter</h4>
  <div class="abs" style="left:832px;top:155px;width:270px;height:66px;border-radius:33px;background:#fff;color:#333;font-size:14px;line-height:66px;padding-left:28px">Email ID</div>
  <svg class="abs" style="left:1040px;top:162px" width="54" height="54"><circle cx="27" cy="27" r="27" fill="#1270c2"/><path d="M15 28l24-11-8 24-4-9z" fill="#fff"/></svg>
  <div class="abs fdot" style="left:838px;top:250px"></div>
  <div class="abs fdot" style="left:898px;top:250px"></div>
  <div class="abs fdot" style="left:958px;top:250px"></div>
  <div class="abs fdot" style="left:1018px;top:250px"></div>
  <div class="abs" style="left:98px;top:353px;width:1002px;height:1px;background:#555"></div>
  <p class="abs" style="left:0;top:370px;width:1200px;text-align:center;font-size:15px">Copyrights@2023.Kestrel Finish Studio.All Rights Reserved</p>
</footer>

</body>
</html>
```